tinyTally Resource Book - 10 maths tasks to do outside

I need a 22 (11 pages back to back) page A6 sized book produced to standard for submission to professional printer. Needs to be as .pdf file showing guide lines and allowances for colour bleed. I have text already written and submitted as attachment in a Word file with margins set to A6 size. The theme of the materials is "Nature Play" so using lots of pictures from nature (Australia preferably) and showing lots of patterns in nature (rocks, leaves, flower petals etc). Some of the tasks refer to specific activities, such as "shadows" and "floating" so would be great to illustrate appropriately. The big emphasis is on learning outside the classroom, getting kids to engage actively with nature. I would like to see the pages as full colour - so not white background. The book itself will be spiral bound along the top edge so a margin of at least 1cm will be required at the top of each page (or the bottom of even numbered pages). Book will be printed on plastic laminated matte paper for outdoor use. Font size needs to be big enough to read. Fonts sizes, alignments and page numbers are all different at the moment and need to be standardised. One photo is included in a page as a sample if you can use it, otherwise disregard. Logo for Wattlebrook Numeracy Guild is also included to have as part of the acknowledgements at the back of the book.

Target Market(s)

Book is for early childhood and preschool teachers.

Industry/Entity Type

Education

Font styles to use
Sans Serif

Requirements
Must have
• Colour and appeal.
Nice to have
• Use of natural colours instead of bright catchy colours but that is your call.
Should not have
• American spelling

```html
<!DOCTYPE html>
<html lang="en-AU">
<head>
<meta charset="utf-8">
<title>11. Informal Units for Measuring Distance</title>
<link rel="stylesheet" href="https://fonts.googleapis.com/css2?family=Nunito:ital,wght@0,800;0,900;1,800;1,900&family=Noto+Sans:wght@400&display=swap">
<style>
  :root {
    --paper: #ffffff;
    --navy: #2b3a8f;
    --ink: #2e2b2a;
    --marker: #d42a2f;
    --sea: #4fc0d9;
    --sea-light: #a9dfe9;
    --sand: #e9e4dc;
    --sand-deep: #ddd6cc;
    --crop: #555555;
  }
  * { margin: 0; padding: 0; box-sizing: border-box; }
  html, body { width: 892px; height: 1200px; overflow: hidden; background: var(--paper); }
  .sheet { position: relative; width: 892px; height: 1200px; }
  .crop-marks { position: absolute; inset: 0; }
  .page-photo {
    position: absolute; left: 53px; top: 53px; width: 785px; height: 1093px;
    background:
      radial-gradient(ellipse 70% 45% at 10% 8%, var(--sea) 0%, rgba(79,192,217,0.6) 45%, rgba(169,223,233,0) 80%),
      linear-gradient(160deg, var(--sea-light) 0%, #cfe7ea 30%, var(--sand) 52%, var(--sand-deep) 100%);
  }
  .title, .outcome {
    position: absolute; left: 53px; width: 785px; text-align: center;
    font-family: "Nunito", sans-serif; color: var(--navy);
    text-shadow: 0 0 3px #fff, 0 0 6px #fff;
  }
  .title { top: 100px; font-size: 46px; font-weight: 900; line-height: 60px; }
  .outcome { top: 243px; font-size: 29px; font-weight: 900; line-height: 42px; }
  .lead {
    position: absolute; left: 125px; font-family: "Nunito", sans-serif;
    font-style: italic; font-weight: 900; font-size: 24px; line-height: 36px;
    color: var(--navy); text-shadow: 0 0 3px #fff;
  }
  .body-copy {
    position: absolute; left: 196px; font-family: "Noto Sans", sans-serif;
    font-size: 30px; line-height: 45px; color: var(--ink);
  }
  .aims { position: absolute; left: 183px; top: 852px; list-style: none;
    font-family: "Noto Sans", sans-serif; font-size: 30px; line-height: 42px; color: var(--ink); }
  .aims li { position: relative; padding-left: 35px; }
  .aims li::before { content: ""; position: absolute; left: 5px; top: 13px; width: 17px; height: 17px;
    background: var(--marker); transform: rotate(45deg); }
</style>
</head>
<body>
<div class="sheet">
  <svg class="crop-marks" width="892" height="1200" viewBox="0 0 892 1200" aria-hidden="true">
    <g stroke="var(--crop)" stroke-width="1" fill="none">
      <path d="M74 36V74H36M53 0V36M0 53H36"/>
      <path d="M818 36V74H856M839 0V36M892 53H856"/>
      <path d="M74 1164V1126H36M53 1200V1164M0 1146H36"/>
      <path d="M818 1164V1126H856M839 1200V1164M892 1146H856"/>
    </g>
  </svg>
  <div class="page-photo" role="img" aria-label="Photograph of a sandy beach with turquoise sea and three weathered wooden posts standing in the sand"></div>

  <h1 class="title">11. Informal Units for<br>Measuring Distance</h1>
  <h2 class="outcome">EYLF – Outcome 5: Children are effective<br>communicators</h2>

  <p class="lead" style="top:344px">Children interact verbally and non-verbally with<br>others for a range of purposes when they...</p>
  <p class="body-copy" style="top:418px">demonstrate an increasing<br>understanding of measurement and<br>number using vocabulary to describe<br>size, length, volume, capacity and<br>names of numbers</p>
  <p class="lead" style="top:644px">Educators promote this learning when they...</p>
  <p class="body-copy" style="top:682px">include real-life resources<br>to promote children’s use of<br>mathematical language</p>
  <p class="lead" style="top:816px">This task provides an opportunity to:</p>
  <ul class="aims">
    <li>explore the concepts of “length” and<br>“measurement”</li>
    <li>use a standard unit of measurement</li>
    <li>develop consistency in measurement<br>by repeating a regular procedure</li>
  </ul>
</div>
</body>
</html>
```